Onboarding Infographic/brochure

We are a small criminal defense firm looking to create some sort of infographic or brochure that we can onboard new clients with. We are currently sending it out via email but want something a bit cooler and fun to send to clients. The information is:

A Few Quick Rules

We are here to help each step of the way. While questions are never discouraged, this letter will answer some of the most common ones we get asked.

Communications

As a client, you should always be in the loop. While we will try to respond to questions as quickly as possible, sometimes we are unable to respond right away. Do not worry - we promise to get back to you soon. Some questions might take some time to research, and a correct answer is better than a quick one.

Appointments

One of the benefits of having an attorney is the ability to discuss your case outside of court, minus the stress and headaches. If you need an appointment, please contact the office.

Appointments must be scheduled in advance. We do not want you to make a special trip to the office only to learn that we are in court or otherwise unavailable.

Jail Visits

If your family member is currently in jail, we take that very seriously. We will visit your loved one and introduce ourselves. While the case is ongoing, we ask that a family member be designated a “contact” person so that messages can be relayed quickly. Never discuss the facts of the case over the phone with someone who is in jail. Jail calls are recorded and we have seen too many cases go south based on remarks made over recorded lines.

Police Reports and Discovery

We will do our best to provide you with copies of everything we receive on your case. Most information will be emailed, so please keep your email address up to date.

Changes in Contact Information

If you move or change numbers during the case, please let us know. It is difficult to help if we are unable to reach you, and helping you is why we are here.

Court Appearances

Cases do not get resolved as quickly as they do on television. Expect there to be several hearings in your case and it may be necessary for you to attend one or more of them. If a hearing is set, you will receive notice of the date and time of each hearing.

Billing and Collections

We understand that this investment was a huge decision for you. As we focus on providing the best representation, we will need for you to stay on schedule with any payment arrangements agreed to at the time of your initial consultation.

Again, thank you for your trust in us. We look forward to getting a fantastic outcome on your case.

Target Market(s)

Criminal defense clients and their families

Industry/Entity Type

Legal

Font styles to use
Serif

Requirements
Must have
• Must incorporate all of the rules we email out. Would like diagrams, images or pictures
Nice to have
• We attached a Welcome brochure. Not sure I want it to look super similar, hence the request for infographic.

```html
<!DOCTYPE html>
<html lang="en">
<head>
<meta charset="utf-8">
<title>Criminal Defense Firm – Client Guide</title>
<link href="https://fonts.googleapis.com/css2?family=Poppins:wght@500;600;700;800&family=Mukta:wght@400;500&display=swap" rel="stylesheet">
<style>
  :root{
    --navy:#143f5d;
    --yellow:#f9d616;
    --white:#ffffff;
    --ink:#1d1d1d;
  }
  *{margin:0;padding:0;box-sizing:border-box}
  html,body{width:848px;height:1200px;overflow:hidden;background:var(--white)}
  .canvas{position:relative;width:848px;height:1200px;overflow:hidden;background:var(--white)}
  .artwork{position:absolute;left:0;top:0}
  .page-title{
    position:absolute;left:42px;top:22px;
    font-family:"Poppins",sans-serif;font-weight:800;font-size:45px;
    color:var(--white);letter-spacing:0.3px;line-height:1.2;
  }
  .rule{position:absolute;text-align:center;color:var(--ink)}
  .rule h2{font-family:"Poppins",sans-serif;font-weight:600;color:var(--navy);white-space:nowrap}
  .rule p{font-family:"Mukta",sans-serif;font-weight:400;margin-left:auto;margin-right:auto}
  .rule--large{width:330px}
  .rule--large h2{font-size:24px;line-height:30px}
  .rule--large p{font-size:16.5px;line-height:28.5px;margin-top:8px;width:252px}
  .rule--small{width:240px}
  .rule--small h2{font-size:17.5px;line-height:27px}
  .rule--small p{font-size:12.8px;line-height:21px;margin-top:8px}
</style>
</head>
<body>
<div class="canvas">
  <svg class="artwork" width="848" height="1200" viewBox="0 0 848 1200" xmlns="http://www.w3.org/2000/svg">
    <path d="M0,0H848V142C720,124 580,114 430,110C280,106 140,100 0,114Z" fill="var(--yellow)"/>
    <path d="M0,0H848V121C700,108 560,102 430,103C280,104 140,82 0,98Z" fill="var(--navy)"/>

    <defs>
      <path id="blob-large" d="M40,40C70,0 130,10 171,40C212,10 272,0 302,40C340,90 345,180 300,230C250,275 92,275 42,230C-3,180 2,90 40,40Z"/>
      <path id="blob-small" d="M30,30C52,0 97,8 128,30C159,8 205,0 227,30C256,68 260,135 227,172C190,206 67,206 30,172C-3,135 1,68 30,30Z"/>
    </defs>

    <!-- 1 Communications -->
    <g transform="translate(64,241)">
      <circle cx="171" cy="40" r="70" fill="var(--navy)"/>
      <use href="#blob-large" fill="var(--white)" stroke="var(--navy)" stroke-width="4"/>
    </g>
    <g fill="var(--yellow)">
      <rect x="212" y="224" width="32" height="24" rx="9"/>
      <path d="M220,246l-4,10l12,-8z"/>
      <rect x="230" y="238" width="30" height="22" rx="9"/>
      <path d="M252,258l5,9l-12,-7z"/>
      <circle cx="221" cy="236" r="2.6" fill="var(--navy)"/>
      <circle cx="228" cy="236" r="2.6" fill="var(--navy)"/>
      <circle cx="235" cy="236" r="2.6" fill="var(--navy)"/>
    </g>

    <!-- 2 Appointments -->
    <g transform="translate(442,241)">
      <circle cx="171" cy="40" r="70" fill="var(--navy)"/>
      <use href="#blob-large" fill="var(--white)" stroke="var(--navy)" stroke-width="4"/>
    </g>
    <g>
      <rect x="595" y="228" width="36" height="32" rx="3" fill="var(--yellow)"/>
      <rect x="601" y="222" width="4" height="10" rx="2" fill="var(--yellow)"/>
      <rect x="621" y="222" width="4" height="10" rx="2" fill="var(--yellow)"/>
      <rect x="595" y="234" width="36" height="3" fill="var(--navy)"/>
      <path d="M604,248l6,6l11,-11" fill="none" stroke="var(--navy)" stroke-width="3.2" stroke-linecap="round" stroke-linejoin="round"/>
    </g>

    <!-- 3 Jail Visits -->
    <g transform="translate(21,579)">
      <circle cx="128" cy="30" r="50" fill="var(--yellow)"/>
      <use href="#blob-small" fill="var(--white)" stroke="var(--yellow)" stroke-width="4"/>
    </g>
    <g fill="var(--navy)">
      <rect x="148" y="566" width="2.5" height="30"/>
      <circle cx="139" cy="580" r="4"/>
      <rect x="133" y="586" width="12" height="11" rx="2"/>
      <circle cx="160" cy="580" r="4"/>
      <rect x="154" y="586" width="12" height="11" rx="2"/>
      <rect x="157" y="588" width="6" height="1.6" fill="var(--yellow)"/>
      <rect x="157" y="591" width="6" height="1.6" fill="var(--yellow)"/>
    </g>

    <!-- 4 Police Reports -->
    <g transform="translate(299,579)">
      <circle cx="128" cy="30" r="50" fill="var(--yellow)"/>
      <use href="#blob-small" fill="var(--white)" stroke="var(--yellow)" stroke-width="4"/>
    </g>
    <g>
      <rect x="415" y="565" width="24" height="30" rx="2" fill="var(--navy)"/>
      <circle cx="427" cy="576" r="5" fill="none" stroke="var(--yellow)" stroke-width="2"/>
      <rect x="420" y="585" width="14" height="2" fill="var(--yellow)"/>
      <rect x="420" y="589" width="14" height="2" fill="var(--yellow)"/>
    </g>

    <!-- 5 Contact Information -->
    <g transform="translate(570,579)">
      <circle cx="128" cy="30" r="50" fill="var(--yellow)"/>
      <use href="#blob-small" fill="var(--white)" stroke="var(--yellow)" stroke-width="4"/>
    </g>
    <circle cx="698" cy="580" r="15" fill="var(--navy)"/>
    <path d="M692,572c1.5,-1 3,-0.6 3.8,0.8l1.4,2.8c0.5,1 0.2,2 -0.6,2.6l-1,0.8c0.9,2.2 2.6,4 4.8,4.9l0.8,-1c0.6,-0.8 1.7,-1.1 2.6,-0.6l2.8,1.4c1.4,0.8 1.7,2.4 0.8,3.7c-1.3,1.8 -3.5,2.5 -5.6,1.7c-5,-2 -8.8,-5.9 -10.7,-10.9c-0.8,-2.1 -0.1,-4.3 0.9,-6.2z" fill="var(--yellow)"/>

    <!-- 6 Court Appearances -->
    <g transform="translate(64,854)">
      <circle cx="171" cy="40" r="70" fill="var(--navy)"/>
      <use href="#blob-large" fill="var(--white)" stroke="var(--navy)" stroke-width="4"/>
    </g>
    <g fill="var(--yellow)">
      <rect x="212" y="840" width="46" height="3"/>
      <circle cx="220" cy="834" r="3.5"/>
      <circle cx="235" cy="834" r="3.5"/>
      <circle cx="250" cy="834" r="3.5"/>
      <rect x="214" y="845" width="42" height="12" rx="1"/>
      <circle cx="235" cy="864" r="4"/>
      <path d="M227,876c0,-5 3.5,-8 8,-8s8,3 8,8z"/>
      <rect x="210" y="876" width="50" height="3"/>
    </g>
    <rect x="218" y="848" width="34" height="2" fill="var(--navy)"/>
    <rect x="218" y="852" width="24" height="2" fill="var(--navy)"/>

    <!-- 7 Billing & Collections -->
    <g transform="translate(442,854)">
      <circle cx="171" cy="40" r="70" fill="var(--navy)"/>
      <use href="#blob-large" fill="var(--white)" stroke="var(--navy)" stroke-width="4"/>
    </g>
    <g>
      <rect x="598" y="836" width="26" height="42" rx="2" fill="var(--yellow)"/>
      <rect x="593" y="836" width="36" height="6" rx="3" fill="var(--yellow)"/>
      <rect x="603" y="846" width="16" height="7" fill="none" stroke="var(--navy)" stroke-width="2"/>
      <rect x="603" y="858" width="16" height="2" fill="var(--navy)"/>
      <rect x="603" y="863" width="12" height="2" fill="var(--navy)"/>
      <rect x="603" y="868" width="16" height="2" fill="var(--navy)"/>
      <rect x="620" y="862" width="14" height="16" rx="1" fill="var(--yellow)" stroke="var(--navy)" stroke-width="1.5"/>
    </g>
  </svg>

  <h1 class="page-title">CRIMINAL DEFENSE FIRM</h1>

  <section class="rule rule--large" style="left:70px;top:296px">
    <h2>1) Communications</h2>
    <p>As a client, you should always be in the loop. While we will try to respond to questions as quickly as possible, sometimes we are unable to respond right away.</p>
  </section>

  <section class="rule rule--large" style="left:448px;top:296px">
    <h2>2) Appointments</h2>
    <p>One of the benefits of having an attorney is the ability to discuss your case outside of court, minus the stress and headaches. If you need an appointment, please contact the office.</p>
  </section>

  <section class="rule rule--small" style="left:29px;top:624px">
    <h2>3) Jail Visits</h2>
    <p style="width:168px">If your family member is currently in jail, we take that very seriously. We will visit your loved one and introduce ourselves.</p>
  </section>

  <section class="rule rule--small" style="left:307px;top:628px">
    <h2>4) Police Reports<br>and Discovery</h2>
    <p style="width:176px">We will do our best to provide you with copies of everything we receive on your case.</p>
  </section>

  <section class="rule rule--small" style="left:578px;top:628px">
    <h2>5) Changes in Contact<br>Information</h2>
    <p style="width:186px">If you move or change numbers during the case, please let us know. It is difficult to help if we are unable to reach you</p>
  </section>

  <section class="rule rule--large" style="left:70px;top:914px">
    <h2>6) Court Appearances</h2>
    <p style="width:250px">Cases do not get resolved as quickly as they do on television. Expect there to be several hearings in your case<br>Do not worry</p>
  </section>

  <section class="rule rule--large" style="left:448px;top:914px">
    <h2>7) Billing &amp; Collections</h2>
    <p style="width:246px">We understand that this investment was a huge decision for you. As we focus on providing the best representation,thank you for your trust in us.</p>
  </section>
</div>
</body>
</html>
```